Business Cards for new orthopaedic surgery practice

My husband and I are starting our own orthopaedic surgery practice. We are looking for a business card that is uniform, but one will have my name/title and the other will have his. You can just create one design with my name on it for now. But when I choose your design as the winning design I will ask that you add another copy with his name/title.

We are looking for classy, simple, elite all in one. We like dark blues/a little gold/yellow. Something that goes with our logo. We want our logo incorporated. Here is all the info you need:
Business name: RV Bone & Vitality Center
Location: 38517 North Willowmere Ave
Palm Crest, FL 33482
Phone: 954-218-4063
Fax: 954-582-7341
Email: info@myrvbonecare.example

Names: Lydia Vance, M.D.
Board Certified Hand and Upper Extremity Surgeon

Ebo Dansu, M.D.
Board Certified Hip & Knee Replacement/General Orthopaedic Surgeon

Can decide what you want to put on the back. Maybe a slogan:
Grounded in Care. Centered on You

I am just going to upload our logo. The only thing is if we select you as the winning design, the location, and phone numbers may change. We will need your help to update that once fully solidified.

Industry/Entity Type

Medical

Contact Information for Business Card

Colors
0054AA
0677BA
7BADD7
CADEEF
E8F1F8
0094D4
00A9DD
6FCCEA
C7EBF8
E9F6FB

Requirements
Must have
• class, appeal,
Should not have
• We want to air on the side of masculine if we are looking at masculine vs. feminine feel. But we still want it classy, sophisticated, and something we will love

```html
<!DOCTYPE html>
<html lang="en">
<head>
<meta charset="UTF-8">
<title>RV Bone &amp; Vitality Center – Business Card</title>
<link rel="stylesheet" href="https://fonts.googleapis.com/css2?family=Montserrat:wght@400;500;600;700&display=swap">
<style>
  :root {
    --navy: #12244c;
    --navy-text: #15294f;
    --gold: #d7993f;
    --gold-rule: #b89e77;
    --lavender: #8f95d6;
    --ink: #111111;
    --gray: #555555;
    --paper: #ffffff;
    --backdrop: #e0e0e0;
  }
  * { margin: 0; padding: 0; box-sizing: border-box; }
  html, body {
    width: 1200px; height: 1200px; overflow: hidden;
    background: var(--backdrop);
    font-family: "Montserrat", sans-serif;
  }
  .card {
    position: absolute;
    left: 179px;
    width: 861px;
    height: 496px;
    box-shadow: 0 14px 22px rgba(0,0,0,0.22);
  }
  .card--front { top: 84px; background: var(--navy); }
  .card--back { top: 622px; background: var(--paper); }

  /* Front */
  .brand-seal {
    position: absolute;
    left: 302px; top: 100px;
    width: 262px; height: 262px;
    border: 2px solid var(--gold);
    border-radius: 50%;
    display: flex; align-items: center; justify-content: center;
    text-align: center;
  }
  .brand-seal__name {
    color: var(--gold);
    font-weight: 600;
    font-size: 25px;
    line-height: 1.3;
    letter-spacing: 0.5px;
  }
  .tagline {
    position: absolute;
    left: 0; right: 0; top: 418px;
    text-align: center;
    color: var(--lavender);
    font-size: 29px;
    font-weight: 500;
  }

  /* Back */
  .practice-name {
    position: absolute;
    left: 45px; top: 33px;
    font-size: 37px; font-weight: 700;
    color: var(--ink);
    letter-spacing: 0.6px;
  }
  .gold-rule {
    position: absolute;
    left: 44px; top: 90px;
    width: 773px; height: 6px;
    background: var(--gold-rule);
  }
  .physician-name {
    position: absolute;
    left: 44px; top: 108px;
    font-size: 33px; font-weight: 600;
    color: var(--navy-text);
  }
  .physician-title {
    position: absolute;
    right: 44px; top: 110px;
    text-align: right;
    font-size: 26px; line-height: 31px;
    color: var(--gray);
    letter-spacing: 0.3px;
  }
  .contact-list {
    position: absolute;
    left: 45px; top: 363px;
    list-style: none;
  }
  .contact-list li {
    display: flex; align-items: center;
    height: 37px;
    font-size: 25px;
    color: var(--gray);
    letter-spacing: 0.2px;
  }
  .contact-list svg {
    width: 26px; height: 26px;
    margin-right: 14px;
    fill: var(--navy-text);
    flex: none;
  }
  .address {
    position: absolute;
    right: 44px; top: 363px;
    text-align: right;
    font-size: 25px; line-height: 37px;
    color: var(--gray);
    font-style: normal;
  }
  .address__web { color: var(--navy-text); }
</style>
</head>
<body>

<section class="card card--front">
  <div class="brand-seal">
    <span class="brand-seal__name">RV Bone &amp;<br>Vitality Center</span>
  </div>
  <p class="tagline">Grounded in Care. Centered on You</p>
</section>

<section class="card card--back">
  <h1 class="practice-name">RV Bone &amp; Vitality Center</h1>
  <div class="gold-rule"></div>
  <h2 class="physician-name">Lydia Vance, M.D.</h2>
  <p class="physician-title">Board Certified Hand and<br>Upper Extremity Surgeon</p>

  <ul class="contact-list">
    <li>
      <svg viewBox="0 0 24 24" aria-hidden="true"><path d="M6.6 10.8c1.4 2.8 3.8 5.1 6.6 6.6l2.2-2.2c.3-.3.7-.4 1-.2 1.1.4 2.3.6 3.6.6.6 0 1 .4 1 1V20c0 .6-.4 1-1 1C10.6 21 3 13.4 3 4c0-.6.4-1 1-1h3.5c.6 0 1 .4 1 1 0 1.3.2 2.5.6 3.6.1.3 0 .7-.2 1L6.6 10.8z"/></svg>
      954-218-4063
    </li>
    <li>
      <svg viewBox="0 0 24 24" aria-hidden="true"><path d="M7 3h10v4H7zM4 8h16c1.1 0 2 .9 2 2v6h-4v5H6v-5H2v-6c0-1.1.9-2 2-2zm4 7v4h8v-4z"/></svg>
      954-582-7341
    </li>
    <li>
      <svg viewBox="0 0 24 24" aria-hidden="true"><path d="M2 5h20v14H2zm2 2v.4l8 5.6 8-5.6V7zm0 2.8V17h16V9.8l-8 5.6z"/></svg>
      info@myrvbonecare.example
    </li>
  </ul>

  <address class="address">
    38517 North Willowmere Ave<br>
    Palm Crest, FL 33482<br>
    <span class="address__web">rvbonecare.example</span>
  </address>
</section>

</body>
</html>
```